Local Mortgage Broker requires DL Flyer

I Require DL sized design for local mortgage broker. Content that will go on the flyer is attached along with the logo.
Looking for a bright & catchy design with that little OOMPH.....on the creative side.
Am looking for a responsive campaign with this style of marketing. The main message is that "We may be able to save thousands of dollars for you, just give us a chance to review your mortgages"

Target Market(s)

All home owners with a mortgage or eople looking to buy their first home.

Industry/Entity Type

Marketing

```html
<!DOCTYPE html>
<html lang="en">
<head>
<meta charset="utf-8">
<title>Finance Solution Flyer</title>
<link href="https://fonts.googleapis.com/css2?family=Arimo:ital,wght@0,400;0,700;1,400&display=swap" rel="stylesheet">
<style>
  :root {
    --stage: #77787b;
    --paper: #ffffff;
    --navy: #2b2a6e;
    --band: #2a2766;
    --ink: #2f2f2f;
    --note: #c9c9c9;
    --fold: #6b6b6b;
    --photo-warm: #d9cfbf;
    --photo-cool: #a9aaa6;
  }
  * { margin: 0; padding: 0; box-sizing: border-box; }
  html, body { width: 1200px; height: 636px; overflow: hidden; }
  body {
    background: var(--stage);
    font-family: "Arimo", Arial, sans-serif;
    position: relative;
  }
  .flyer {
    position: absolute;
    left: 63px; top: 62px;
    width: 1076px; height: 512px;
    background: var(--paper);
    overflow: hidden;
  }
  .hero-photo {
    position: absolute;
    left: 630px; top: 0;
    width: 446px; height: 448px;
    background:
      linear-gradient(90deg, var(--paper) 0%, rgba(255,255,255,0.6) 18%, rgba(255,255,255,0) 40%),
      linear-gradient(160deg, #ece8e0 0%, var(--photo-warm) 45%, var(--photo-cool) 100%);
  }
  .headline {
    position: absolute;
    left: 45px; top: 40px;
    font-size: 31px; font-weight: 700;
    color: var(--navy);
    letter-spacing: -0.2px;
  }
  .intro {
    position: absolute;
    left: 45px; top: 92px;
    width: 230px;
    font-size: 17px; line-height: 25.3px;
    color: var(--ink);
  }
  .services {
    position: absolute;
    left: 285px; top: 94px;
    list-style: none;
  }
  .services li {
    display: flex; align-items: center;
    font-size: 19px; font-weight: 700;
    line-height: 29px;
    color: var(--navy);
  }
  .services svg { width: 16px; height: 16px; margin-right: 9px; }
  .tagline {
    position: absolute;
    left: 289px; top: 235px;
    width: 356px; height: 70px;
    background: var(--note);
    padding: 11px 18px;
    font-size: 18px; font-style: italic; line-height: 24px;
    text-transform: uppercase;
    color: var(--ink);
  }
  .tagline-fold {
    position: absolute;
    left: 613px; top: 305px;
    width: 32px; height: 28px;
  }
  .promise {
    position: absolute;
    left: 289px; top: 330px;
    width: 350px;
    font-size: 19px; font-style: italic; line-height: 24px;
    color: var(--ink);
  }
  .contact-band {
    position: absolute;
    left: 0; bottom: 0;
    width: 100%; height: 64px;
    background: var(--band);
    display: flex; align-items: center; justify-content: center;
    color: #fff;
    font-size: 27px;
    white-space: nowrap;
  }
  .contact-band strong { font-weight: 700; }
  .contact-band .web { margin-left: 10px; }
</style>
</head>
<body>
  <section class="flyer">
    <div class="hero-photo" role="img" aria-label="Photo of a couple embracing, seen from behind, looking at a new two-storey house"></div>

    <h1 class="headline">Find the right Finance Solution</h1>

    <p class="intro">Whether you are looking to buy your first home, renovate, refinance or invest, we’re here to negotiate the right finance for you. We’re a one-stop shop with hundreds of loan options available from across Australia’s leading lenders and we’ll work with you to find the right finance solution to meet your needs.</p>

    <ul class="services">
      <li><svg viewBox="0 0 16 16"><path d="M2 2 L14 8 L2 14" fill="none" stroke="#2b2a6e" stroke-width="1.8"/></svg>Refinance existing Mortgage</li>
      <li><svg viewBox="0 0 16 16"><path d="M2 2 L14 8 L2 14" fill="none" stroke="#2b2a6e" stroke-width="1.8"/></svg>Purchase First Home</li>
      <li><svg viewBox="0 0 16 16"><path d="M2 2 L14 8 L2 14" fill="none" stroke="#2b2a6e" stroke-width="1.8"/></svg>Purchase Investment Property</li>
      <li><svg viewBox="0 0 16 16"><path d="M2 2 L14 8 L2 14" fill="none" stroke="#2b2a6e" stroke-width="1.8"/></svg>Upgrade or Renovate existing Property</li>
    </ul>

    <div class="tagline">The right loan to suit your individual requirements.</div>
    <svg class="tagline-fold" viewBox="0 0 32 28"><polygon points="0,0 32,0 0,28" fill="#6b6b6b"/></svg>

    <p class="promise">We are confident that we may be able to save you thousands of dollars over the term of your loan by simply reviewing your existing home loan.</p>

    <footer class="contact-band">
      <span>Call us on <strong>0400 000 123</strong> to find out how !</span>
      <strong class="web">www.homeloanpath.com.au</strong>
    </footer>
  </section>
</body>
</html>
```